KORVAL:advise Business Cards

We need a business card design for KORVAL:advise (Logo Attached), a management consultancy specialized in brand & business building.

Design should be clean, smart and a touch of innnovation without being gimmicky.

The details on the card should be:
Name: Tomas Velduren
Title: Managing Director
Address: 42 Marlowe Pier, Tarn Vessel Tower, Singapore 073926
Tel: +6285927461082
email: tv@korvaladvise.example
website: korvaladvise.example

For further background on corporate identity, please check www.korvaladvise.example
Updates

Dear all,

Many thanks for the submissions so far! I gave feedback to those designs that I prefer at this stage.

Overall I see that my preference goes into the direction that 'less is more' and 'simple is beautiful'

Please create uniqueness and standout by the simplicity and attraction of the overall concept and design.

Many thanks and please shout incase of questions!

Tomas

Industry/Entity Type

Business

```html
<!DOCTYPE html>
<html lang="en">
<head>
<meta charset="utf-8">
<title>Korval Advise Business Cards</title>
<link rel="stylesheet" href="https://fonts.googleapis.com/css2?family=PT+Sans:wght@400;700&family=Open+Sans:wght@400;600&display=swap">
<style>
  :root {
    --ink: #4a4a4c;
    --orange: #ff6600;
    --paper: #ffffff;
    --backdrop: #ececec;
    --edge: #7a7a7a;
  }
  * { box-sizing: border-box; margin: 0; padding: 0; }
  html, body { width: 1174px; height: 1200px; overflow: hidden; }
  body {
    position: relative;
    background: var(--backdrop);
    font-family: "Open Sans", sans-serif;
    color: var(--ink);
  }
  .card {
    position: absolute;
    width: 942px;
    height: 537px;
    background: var(--paper);
    border: 1px solid var(--edge);
    overflow: hidden;
  }
  .card--front { left: 40px; top: 39px; }
  .card--back { left: 203px; top: 619px; height: 538px; }

  .brand {
    position: absolute;
    left: 0; right: 0;
    text-align: center;
    font-family: "Open Sans", sans-serif;
    font-weight: 600;
    font-size: 70px;
    letter-spacing: -0.5px;
    color: var(--ink);
    line-height: 1;
  }
  .card--front .brand { top: 102px; }
  .card--back .brand { top: 236px; }

  .identity {
    position: absolute;
    top: 270px; left: 0; right: 0;
    text-align: center;
    font-family: "PT Sans", sans-serif;
    font-size: 23px;
    line-height: 1.2;
  }
  .identity__name { font-weight: 700; font-size: 27px; color: var(--ink); }
  .identity__title { color: var(--orange); }

  .rule {
    position: absolute;
    left: 0; right: 0; top: 329px;
    height: 4px;
    background: var(--ink);
  }
  .band {
    position: absolute;
    left: 0; right: 0; top: 339px; bottom: 0;
    background: var(--orange);
    color: var(--paper);
    font-size: 23px;
  }
  .address {
    position: absolute;
    right: 514px; top: 46px;
    text-align: right;
    font-style: normal;
    line-height: 41px;
  }
  .divider {
    position: absolute;
    left: 451px; top: 38px;
    width: 1px; height: 133px;
    background: rgba(255,255,255,0.75);
  }
  .contacts {
    position: absolute;
    left: 478px; top: 34px;
    list-style: none;
  }
  .contacts li {
    display: flex;
    align-items: center;
    gap: 10px;
    height: 50px;
  }
  .contacts svg { width: 18px; height: 18px; flex: none; }

  .web {
    position: absolute;
    top: 396px; left: 0; right: 0;
    text-align: center;
    font-size: 24px;
    letter-spacing: 0.3em;
    color: var(--ink);
  }
</style>
</head>
<body>
  <section class="card card--front">
    <p class="brand">Korval Advise</p>
    <p class="identity"><span class="identity__name">Tomas Velduren,</span> <span class="identity__title">Managing Director</span></p>
    <div class="rule"></div>
    <div class="band">
      <address class="address">42 Marlowe Pier, Tarn<br>Vessel Tower<br>Singapore 073926</address>
      <div class="divider"></div>
      <ul class="contacts">
        <li>
          <svg viewBox="0 0 20 20" aria-hidden="true"><path d="M5 2l3 4-2 2c1 2.5 3.5 5 6 6l2-2 4 3-2 3C9 17 3 11 2 4z" fill="none" stroke="#fff" stroke-width="1.6"/></svg>
          <span>+6285927461082</span>
        </li>
        <li>
          <svg viewBox="0 0 20 20" aria-hidden="true"><rect x="1.5" y="5" width="17" height="11" fill="#fff"/><path d="M1.5 5l8.5 6 8.5-6" fill="none" stroke="#ff6600" stroke-width="1.5"/></svg>
          <span>tv@korvaladvise.example</span>
        </li>
        <li>
          <svg viewBox="0 0 20 20" aria-hidden="true"><g fill="none" stroke="#fff" stroke-width="1.4"><circle cx="10" cy="10" r="8"/><ellipse cx="10" cy="10" rx="3.5" ry="8"/><path d="M2 10h16M3.5 5.5h13M3.5 14.5h13"/></g></svg>
          <span>www.korvaladvise.example</span>
        </li>
      </ul>
    </div>
  </section>

  <section class="card card--back">
    <p class="brand">Korval Advise</p>
    <p class="web">www.korvaladvise.example</p>
  </section>
</body>
</html>
```